Redesign Comparisson chart - make modern and effective

Use your imaginations to make a powerful distinction between KMV & other holistic modalities. There are 7 elements physical, mental, emotional, energetic, subconscious, superconscious and before and after testing.
We want it to be obvious that KMV is the only modality that works on all these elements simultaneously. We do not want to include any chakras as we want this information to be accepted by a wide range of people and belief systems.'

We want it to look simple but effective. Professional but powerful. We want KMV to stand out even of you eye just passed over i.
Updates

Hi everyone, thanks for your submissions so far. Basically what this image is meant to represent is a comparison chart between all the modalities There are 5 elements physical, mental, emotional, subconscious and superconscious. we want to reflect that KMV is the only modality that works on all these elements simultaneously. As we want the concept to be accepted and not considered woo woo, we want to steer away from chakras.

Target Market(s)

Professionals

Industry/Entity Type

Professional services

Font styles to use
Sans Serif
Other font styles liked:
• Poppins Monserratt

Colors
0094D4
00A9DD
6FCCEA
C7EBF8
E9F6FB

Requirements
Must have
• Clear/professional and clean look. Brand colours and logos. All typography and formats must be cohesive.
Nice to have
• More easy to read, different layout
Should not have
• Do not change the data just the way its presented. No chakras

```html
<!DOCTYPE html>
<html lang="en">
<head>
<meta charset="utf-8">
<title>KMV – Modality Comparison Chart</title>
<link href="https://fonts.googleapis.com/css2?family=Poppins:ital,wght@0,400;0,500;0,600;0,700;1,600&display=swap" rel="stylesheet">
<style>
  :root{
    --brand:#2fb5e6;
    --brand-light:#7dd8f7;
    --navy:#1b5470;
    --ink:#1d2330;
    --bg:#eef2fa;
    --tube:#e2e5ed;
    --pink:#d573ad;
    --purple:#826cad;
    --yellow:#e9d152;
    --orange:#f2a035;
    --green:#62ae46;
    --blue:#62bedd;
    --red:#db4a3f;
  }
  *{margin:0;padding:0;box-sizing:border-box}
  html,body{width:1200px;height:825px;overflow:hidden;background:#fff}
  body{font-family:"Poppins",sans-serif;color:var(--ink)}
  .canvas{width:1200px;height:825px;overflow:hidden;position:relative}
  .board{position:absolute;left:0;top:0;width:2322px;height:1596px;transform:scale(0.51680);transform-origin:0 0;background:#fff}
  .body-band{position:absolute;left:0;top:210px;width:2322px;height:1386px;background:var(--bg)}
  .chart{position:absolute;left:0;top:0}

  .headline{position:absolute;left:142px;top:66px;font-size:38px;font-weight:600;line-height:46px;color:var(--brand);letter-spacing:.6px}
  .brand{position:absolute;left:990px;top:86px;display:flex;align-items:center;gap:12px;white-space:nowrap}
  .brand-dot{width:24px;height:24px;border-radius:50%;background:var(--brand)}
  .brand-name{font-size:25px;font-weight:600;line-height:32px;color:var(--brand)}
  .pledge{position:absolute;left:1340px;top:62px;width:930px;text-align:center;font-size:16.5px;font-weight:600;font-style:italic;line-height:25.5px;color:var(--ink)}

  .pill{position:absolute;width:220px;height:29px;border-radius:15px;background:var(--navy);color:#fff;font-size:18.5px;font-weight:500;letter-spacing:.4px;display:flex;align-items:center;justify-content:center;text-align:center;line-height:19px}
  .pill.tall{height:51px;border-radius:26px}
  .pill.short{width:162px}
  .pill.wide{width:244px}

  .note{position:absolute;width:266px}
  .note h3{font-size:28px;font-weight:600;line-height:33px;letter-spacing:.8px}
  .note p{font-size:15.2px;line-height:18.6px;text-align:justify;text-align-last:left;margin-top:2px}
  .note.left{left:826px;text-align:right}
  .note.right{left:1230px}
  .c-pink{color:var(--pink)} .c-purple{color:var(--purple)} .c-yellow{color:var(--yellow)}
  .c-orange{color:var(--orange)} .c-green{color:var(--green)} .c-blue{color:var(--blue)} .c-red{color:var(--red)}

  .footer{position:absolute;left:958px;top:1522px;display:flex;align-items:center;height:40px}
  .footer-dot{width:28px;height:28px;border-radius:50%;background:var(--brand);margin-right:14px}
  .footer-name{font-size:28px;font-weight:700;color:var(--brand)}
  .footer-rule{width:2px;height:34px;background:var(--brand);margin:0 14px}
  .footer-url{font-size:22px;font-weight:600;color:var(--brand)}
</style>
</head>
<body>
<div class="canvas">
 <div class="board">
  <div class="body-band"></div>

  <h1 class="headline">CHOOSE KMV FOR FAST, IMMEDIATE AND<br>POWERFUL RESULTS</h1>
  <div class="brand"><span class="brand-dot"></span><span class="brand-name">Kinetic Mind Vitality</span></div>
  <p class="pledge">I MUST EXPERIENCE HEALING ON ALL LEVELS, I AM NOT JUST A BODY.<br>I WANT TO LEARN HOW TO HEAL MYSELF, SO I'M NOT DEPENDENT ON OTHERS.<br>I WANT TO RELEASE ALL MY EMOTIONAL AND MENTAL BLOCKS, SO I CAN BE THE BEST VERSION OF MYSELF.</p>

  <svg class="chart" width="2322" height="1596" viewBox="0 0 2322 1596" aria-hidden="true">
   <defs>
    <clipPath id="tube-clip" clipPathUnits="objectBoundingBox"><rect width="1" height="1" rx="0.5" ry="0.0553"/></clipPath>
    <clipPath id="core-clip" clipPathUnits="objectBoundingBox"><rect width="1" height="1" rx="0.5" ry="0.0237"/></clipPath>
   </defs>

   <g stroke="var(--navy)" stroke-width="2.5" fill="none">
    <line x1="380" y1="325" x2="380" y2="400"/><line x1="626" y1="325" x2="626" y2="400"/>
    <line x1="256" y1="702" x2="256" y2="773"/><line x1="503" y1="702" x2="503" y2="775"/>
    <line x1="380" y1="1017" x2="380" y2="1081"/><line x1="626" y1="1017" x2="626" y2="1081"/>
    <line x1="256" y1="1383" x2="256" y2="1453"/><line x1="503" y1="1383" x2="503" y2="1453"/>
    <line x1="1852" y1="326" x2="1852" y2="400"/><line x1="2098" y1="326" x2="2098" y2="400"/>
    <line x1="1729" y1="702" x2="1729" y2="773"/><line x1="1975" y1="702" x2="1975" y2="773"/>
    <line x1="1729" y1="1011" x2="1729" y2="1081"/><line x1="1975" y1="1011" x2="1975" y2="1081"/>
    <line x1="1852" y1="1383" x2="1852" y2="1461"/><line x1="2098" y1="1383" x2="2098" y2="1461"/>
    <line x1="1163" y1="1262" x2="1163" y2="1350"/>
   </g>

   <g clip-path="url(#tube-clip)"><rect x="235" y="372" width="42" height="380" fill="var(--tube)"/><rect x="235" y="677" width="42" height="75" fill="var(--red)"/></g>
   <g clip-path="url(#tube-clip)"><rect x="359" y="372" width="42" height="380" fill="var(--tube)"/><rect x="359" y="677" width="42" height="75" fill="var(--red)"/><rect x="359" y="593" width="42" height="75" fill="var(--blue)"/></g>
   <g clip-path="url(#tube-clip)"><rect x="482" y="372" width="42" height="380" fill="var(--tube)"/><rect x="482" y="677" width="42" height="75" fill="var(--red)"/><rect x="482" y="593" width="42" height="75" fill="var(--blue)"/><rect x="482" y="508" width="42" height="76" fill="var(--orange)"/></g>
   <g clip-path="url(#tube-clip)"><rect x="605" y="372" width="42" height="380" fill="var(--tube)"/><rect x="605" y="677" width="42" height="75" fill="var(--red)"/><rect x="605" y="593" width="42" height="75" fill="var(--orange)"/></g>

   <g clip-path="url(#tube-clip)"><rect x="235" y="1053" width="42" height="381" fill="var(--tube)"/><rect x="235" y="1358" width="42" height="76" fill="var(--red)"/><rect x="235" y="1274" width="42" height="75" fill="var(--pink)"/></g>
   <g clip-path="url(#tube-clip)"><rect x="359" y="1053" width="42" height="381" fill="var(--tube)"/><rect x="359" y="1358" width="42" height="76" fill="var(--red)"/><rect x="359" y="1274" width="42" height="75" fill="var(--orange)"/><rect x="359" y="1189" width="42" height="76" fill="var(--pink)"/></g>
   <g clip-path="url(#tube-clip)"><rect x="482" y="1053" width="42" height="381" fill="var(--tube)"/><rect x="482" y="1358" width="42" height="76" fill="var(--red)"/><rect x="482" y="1274" width="42" height="75" fill="var(--yellow)"/><rect x="482" y="1189" width="42" height="76" fill="var(--pink)"/></g>
   <g clip-path="url(#tube-clip)"><rect x="605" y="1053" width="42" height="381" fill="var(--tube)"/><rect x="605" y="1358" width="42" height="76" fill="var(--red)"/><rect x="605" y="1274" width="42" height="75" fill="var(--blue)"/><rect x="605" y="1189" width="42" height="76" fill="var(--yellow)"/><rect x="605" y="1104" width="42" height="76" fill="var(--pink)"/></g>

   <g clip-path="url(#tube-clip)"><rect x="1708" y="372" width="42" height="380" fill="var(--tube)"/><rect x="1708" y="677" width="42" height="75" fill="var(--red)"/><rect x="1708" y="593" width="42" height="75" fill="var(--orange)"/><rect x="1708" y="508" width="42" height="76" fill="var(--yellow)"/><rect x="1708" y="423" width="42" height="76" fill="var(--pink)"/></g>
   <g clip-path="url(#tube-clip)"><rect x="1831" y="372" width="42" height="380" fill="var(--tube)"/><rect x="1831" y="677" width="42" height="75" fill="var(--orange)"/></g>
   <g clip-path="url(#tube-clip)"><rect x="1954" y="372" width="42" height="380" fill="var(--tube)"/><rect x="1954" y="677" width="42" height="75" fill="var(--orange)"/><rect x="1954" y="593" width="42" height="75" fill="var(--pink)"/></g>
   <g clip-path="url(#tube-clip)"><rect x="2077" y="372" width="42" height="380" fill="var(--tube)"/><rect x="2077" y="677" width="42" height="75" fill="var(--yellow)"/><rect x="2077" y="593" width="42" height="75" fill="var(--purple)"/></g>

   <g clip-path="url(#tube-clip)"><rect x="1708" y="1053" width="42" height="381" fill="var(--tube)"/><rect x="1708" y="1358" width="42" height="76" fill="var(--blue)"/></g>
   <g clip-path="url(#tube-clip)"><rect x="1831" y="1053" width="42" height="381" fill="var(--tube)"/><rect x="1831" y="1358" width="42" height="76" fill="var(--blue)"/><rect x="1831" y="1274" width="42" height="75" fill="var(--pink)"/></g>
   <g clip-path="url(#tube-clip)"><rect x="1954" y="1053" width="42" height="381" fill="var(--tube)"/><rect x="1954" y="1358" width="42" height="76" fill="var(--blue)"/><rect x="1954" y="1274" width="42" height="75" fill="var(--yellow)"/></g>
   <g clip-path="url(#tube-clip)"><rect x="2077" y="1053" width="42" height="381" fill="var(--tube)"/><rect x="2077" y="1358" width="42" height="76" fill="var(--blue)"/><rect x="2077" y="1274" width="42" height="75" fill="var(--yellow)"/><rect x="2077" y="1189" width="42" height="76" fill="var(--pink)"/></g>

   <g clip-path="url(#core-clip)">
    <rect x="1138" y="255" width="50" height="1055" fill="var(--tube)"/>
    <rect x="1138" y="340" width="50" height="116" fill="var(--pink)"/>
    <rect x="1138" y="340" width="50" height="18" fill="#c25a98"/>
    <rect x="1138" y="467" width="50" height="131" fill="var(--purple)"/>
    <rect x="1138" y="609" width="50" height="131" fill="var(--yellow)"/>
    <rect x="1138" y="751" width="50" height="131" fill="var(--orange)"/>
    <rect x="1138" y="893" width="50" height="132" fill="var(--green)"/>
    <rect x="1138" y="1036" width="50" height="131" fill="var(--blue)"/>
    <rect x="1138" y="1178" width="50" height="132" fill="var(--red)"/>
   </g>
   <circle cx="1163" cy="314" r="37" fill="var(--brand-light)"/>
   <path d="M1145 315 l12 12 l22 -24" stroke="#fff" stroke-width="8" stroke-linecap="round" stroke-linejoin="round" fill="none"/>
   <circle cx="1163" cy="1410" r="61" fill="var(--brand)"/>

   <g fill="none" stroke-width="1.6">
    <g stroke="var(--pink)"><line x1="1218" y1="326" x2="1218" y2="452"/><line x1="1188" y1="380" x2="1218" y2="380"/></g>
    <g stroke="var(--purple)"><line x1="1104" y1="470" x2="1104" y2="595"/><line x1="1104" y1="520" x2="1138" y2="520"/></g>
    <g stroke="var(--yellow)"><line x1="1218" y1="611" x2="1218" y2="748"/><line x1="1188" y1="660" x2="1218" y2="660"/></g>
    <g stroke="var(--orange)"><line x1="1104" y1="755" x2="1104" y2="880"/><line x1="1104" y1="805" x2="1138" y2="805"/></g>
    <g stroke="var(--green)"><line x1="1218" y1="871" x2="1218" y2="995"/><line x1="1188" y1="948" x2="1218" y2="948"/></g>
    <g stroke="var(--blue)"><line x1="1104" y1="1039" x2="1104" y2="1164"/><line x1="1104" y1="1088" x2="1138" y2="1088"/></g>
    <g stroke="var(--red)"><line x1="1218" y1="1137" x2="1218" y2="1262"/><line x1="1188" y1="1222" x2="1218" y2="1222"/></g>
   </g>

   <g fill="var(--navy)">
    <circle cx="380" cy="400" r="6"/><circle cx="626" cy="400" r="6"/><circle cx="256" cy="702" r="6"/><circle cx="503" cy="702" r="6"/>
    <circle cx="380" cy="1081" r="6"/><circle cx="626" cy="1081" r="6"/><circle cx="256" cy="1383" r="6"/><circle cx="503" cy="1383" r="6"/>
    <circle cx="1852" cy="400" r="6"/><circle cx="2098" cy="400" r="6"/><circle cx="1729" cy="702" r="6"/><circle cx="1975" cy="702" r="6"/>
    <circle cx="1729" cy="1081" r="6"/><circle cx="1975" cy="1081" r="6"/><circle cx="1852" cy="1383" r="6"/><circle cx="2098" cy="1383" r="6"/>
    <circle cx="1163" cy="1262" r="6"/>
   </g>
  </svg>

  <div class="pill" style="left:270px;top:296px">PSYCHIC INTUITIVE</div>
  <div class="pill" style="left:516px;top:296px">ACUPUNCTURE</div>
  <div class="pill" style="left:146px;top:773px">MASSAGE</div>
  <div class="pill" style="left:146px;top:809px">YOGA</div>
  <div class="pill" style="left:146px;top:845px">NATROPATHY</div>
  <div class="pill" style="left:146px;top:881px">AYURVEDIC MEDICINE</div>
  <div class="pill" style="left:146px;top:917px">WESTERN MEDICINE</div>
  <div class="pill tall" style="left:393px;top:775px">FAMILY<br>CONSTELLATION</div>
  <div class="pill" style="left:270px;top:988px">CHINESE MEDICINE</div>
  <div class="pill short" style="left:545px;top:988px">EFT</div>
  <div class="pill" style="left:146px;top:1453px">NUTRITIONAL HEALING</div>
  <div class="pill" style="left:393px;top:1453px">KINESIOLOGY</div>
  <div class="pill" style="left:393px;top:1490px">BOWEN THERAPY</div>

  <div class="pill" style="left:1742px;top:262px">REIKI</div>
  <div class="pill" style="left:1742px;top:297px">CRYSTAL HEALING</div>
  <div class="pill" style="left:1988px;top:297px">THETA HEALING</div>
  <div class="pill" style="left:1619px;top:773px">CHIROPRACTIC</div>
  <div class="pill" style="left:1865px;top:773px">ENERGY MEDICINE</div>
  <div class="pill" style="left:1619px;top:982px">PSHYCHOLOGY</div>
  <div class="pill" style="left:1865px;top:946px">HYPNOTHERAPY</div>
  <div class="pill" style="left:1865px;top:982px">INNER CHILD HEALING</div>
  <div class="pill tall" style="left:1742px;top:1461px">MINDFULLNESS<br>MEDITATION</div>
  <div class="pill" style="left:1742px;top:1521px">LIFE COACHING</div>
  <div class="pill" style="left:1988px;top:1461px">NLP</div>
  <div class="pill" style="left:1988px;top:1497px">TIMELINE THERAPHY</div>

  <div class="pill wide" style="left:1041px;top:1480px">KINETIC MIND VITALITY</div>

  <div class="note right" style="top:318px">
   <h3 class="c-pink">BEFORE &amp; AFTER<br>TESTING</h3>
   <p>KMV is the only modality the enables you to provide before and after results, which are documented by us, and analysed by you with our help.</p>
  </div>
  <div class="note left" style="top:462px">
   <h3 class="c-purple">SUPERCONSCIOUS</h3>
   <p>KMV is the only modality the enables you to access and heal your superconscious mind yourself.</p>
  </div>
  <div class="note right" style="top:603px">
   <h3 class="c-yellow">SUBCONSCIOUS</h3>
   <p>Some modalities, like Kinesiology, access your subconscious through muscle testing.<br>KMV empowers you to access your own subconscious and heal it yourself.</p>
  </div>
  <div class="note left" style="top:747px">
   <h3 class="c-orange">ENERGETIC</h3>
   <p>Most modalities try to move the energy in your body for you. KMV enables and empowers you to do it yourself.</p>
  </div>
  <div class="note right" style="top:863px">
   <h3 class="c-green">EMOTIONAL</h3>
   <p>KMV is the only modality that engages your emotions on a physical level. Emotions get stuck in your body and can cause illness over time if left unchecked. KMV enables you you experience fast and powerful emotional releasing</p>
  </div>
  <div class="note left" style="top:1031px">
   <h3 class="c-blue">MENTAL</h3>
   <p>KMV enables you to use your own consciousness to self-heal. We don't give you advice or coaching, we allow your mind to heal itself.</p>
  </div>
  <div class="note right" style="top:1129px">
   <h3 class="c-red">PHYSICAL</h3>
   <p>Most modalities, including, a western medicine, focus on and treat the physical body only. The KMV process enables you to engage in healing your own body during the session. There is no muscle testing, no hands-on healing and no herbal remedies or medicines.</p>
  </div>

  <div class="footer">
   <span class="footer-dot"></span><span class="footer-name">Brightwell</span><span class="footer-rule"></span><span class="footer-url">www.brightwell.com.au</span>
  </div>
 </div>
</div>
</body>
</html>
```